Singer/Songwriter/performer wants Retro Art Poster

I'm looking for a beautiful iconic art poster design that incorporates an image of me, my name and possibly a quote...could be a heavily treated image or an illustration. Something that people will want to put on their walls in their homes. Could have a vintage vibe like the Red Harbor record label Jazz posters.It could include a press quote ... you can find high res images to use and more information about me with music here https://lisarichardsmusic.com/epk-bioI've included a couple of examples... But I'm open to other ideas. Musically ... here's a description of what I do.."With an instantly identifiable vocal timbre and an elastic sense of phrasing, Moira has been called a singer's singer. Her songs are a melting pot mixture of jazz, folk, blues, pop, rock and country - her own brand of adventurous folk art.. She's released 6 albums and is working on her 7th."
People who enjoy my music and want to buy something that represents what I do that isn't actual music
Designer to choose colors to be used in the design.

```html
<!DOCTYPE html>
<html lang="en">
<head>
<meta charset="utf-8">
<title>Moira Dunne — Poster</title>
<link rel="stylesheet" href="https://fonts.googleapis.com/css2?family=Arimo:ital,wght@1,400;1,700&family=Pinyon+Script&display=swap">
<style>
  :root {
    --poster-orange: #f05a30;
    --paper-white: #ffffff;
    --ink-black: #000000;
    --studio-white: #f3f3f3;
    --studio-grey: #d9d9d9;
    --suit-grey: #4a4746;
    --suit-dark: #2e2c2b;
  }
  html, body {
    margin: 0;
    padding: 0;
    overflow: hidden;
    background: var(--poster-orange);
  }
  .poster {
    position: relative;
    width: 849px;
    height: 1200px;
    background: var(--poster-orange);
    overflow: hidden;
  }
  .shape {
    position: absolute;
    border-radius: 50%;
    overflow: hidden;
  }
  .portrait-circle {
    left: 0; top: 0;
    width: 418px; height: 418px;
  }
  .name-circle {
    left: 430px; top: 0;
    width: 419px; height: 419px;
    background: var(--paper-white);
  }
  .quote-oval {
    left: 0; top: 600px;
    width: 275px; height: 600px;
    background: var(--paper-white);
  }
  .legs-oval {
    left: 287px; top: 600px;
    width: 275px; height: 600px;
  }
  .black-oval {
    left: 574px; top: 600px;
    width: 275px; height: 600px;
    background: var(--ink-black);
  }
  .photo-fill {
    display: block;
    width: 100%;
    height: 100%;
  }
  .name-ring {
    position: absolute;
    left: 430px; top: 0;
    width: 419px; height: 419px;
    overflow: visible;
  }
  .name-ring text {
    font-family: "Pinyon Script", cursive;
    font-size: 88px;
    fill: var(--ink-black);
  }
  .press-quote {
    position: absolute;
    left: 36px;
    top: 1035px;
    width: 210px;
    margin: 0;
    font-family: Arimo, Arial, sans-serif;
    font-style: italic;
    font-size: 14.6px;
    line-height: 17px;
    color: var(--ink-black);
    text-align: center;
  }
  .press-quote strong { font-weight: 700; }
</style>
</head>
<body>
<main class="poster">
  <div class="shape portrait-circle">
    <svg class="photo-fill" viewBox="0 0 418 418" role="img" aria-label="Black and white portrait of the singer in a pinstripe suit, head tilted back, eyes closed">
      <defs>
        <linearGradient id="portraitTone" x1="0.1" y1="0" x2="0.45" y2="1">
          <stop offset="0" stop-color="var(--studio-white)"/>
          <stop offset="0.5" stop-color="var(--studio-grey)"/>
          <stop offset="0.68" stop-color="var(--suit-grey)"/>
          <stop offset="1" stop-color="var(--suit-dark)"/>
        </linearGradient>
      </defs>
      <rect width="418" height="418" fill="url(#portraitTone)"/>
    </svg>
  </div>

  <div class="shape name-circle"></div>
  <svg class="name-ring" viewBox="0 0 419 419" aria-label="Moira Dunne">
    <defs>
      <path id="ringPath" d="M110.5 38 A198 198 0 1 0 405.6 181.9"/>
    </defs>
    <text><textPath href="#ringPath" textLength="850" lengthAdjust="spacing">MOIRA DUNNE</textPath></text>
  </svg>

  <div class="shape quote-oval"></div>
  <p class="press-quote">“<strong>Moira Dunne</strong> is a<br>simple yet powerful<br>songwriter who has<br>beautifully encapsulated<br>the intricacies of the<br>human condition.”</p>

  <div class="shape legs-oval">
    <svg class="photo-fill" viewBox="0 0 275 600" role="img" aria-label="Black and white photo of crossed legs in pinstripe trousers and denim platform shoes">
      <defs>
        <linearGradient id="legsTone" x1="0.2" y1="0" x2="0.7" y2="1">
          <stop offset="0" stop-color="var(--suit-dark)"/>
          <stop offset="0.55" stop-color="var(--suit-grey)"/>
          <stop offset="0.8" stop-color="var(--suit-dark)"/>
          <stop offset="1" stop-color="var(--studio-grey)"/>
        </linearGradient>
        <radialGradient id="legsLight" cx="0.1" cy="0.85" r="0.45">
          <stop offset="0" stop-color="var(--studio-white)" stop-opacity="0.9"/>
          <stop offset="1" stop-color="var(--studio-white)" stop-opacity="0"/>
        </radialGradient>
      </defs>
      <rect width="275" height="600" fill="url(#legsTone)"/>
      <rect width="275" height="600" fill="url(#legsLight)"/>
    </svg>
  </div>

  <div class="shape black-oval"></div>
</main>
</body>
</html>
```